Business Card Design Project - del varosi group

dear Sirs

we need business card design for our group ( DEL Varosi Group ) , i have got the Logo design of our group from pixel harbor in previous , so all need details relating to our group i think available with you, as well as the the chosen logo design

we hope to provide us with business card logo that to be appropaite and satisfactory to us .

thanks

note : logo design of our group is attached .
Updates

Reason: please extend the deadline of my project for additional 15 days because i didn't received appropriate design for our gruop yet . kindly beaware that i have received 77 design till now , supossed to send me 200-250 design at least . thanks

Target Market(s)

contents

name : Kerem EL Nadiri

position : Operation Manager

Industry/Entity Type

Business

Requirements
Must have

• person name

group logo
Nice to have
• logo color matching with back background

```html
<!DOCTYPE html>
<html lang="en">
<head>
<meta charset="utf-8">
<title>DEL Varosi Group – Business Cards</title>
<link rel="stylesheet" href="https://fonts.googleapis.com/css2?family=Source+Sans+3:wght@400;600;700&display=swap">
<style>
  :root {
    --backdrop: #b08a2e;
    --card: #ffffff;
    --brand-blue: #0a5a9c;
    --name-blue: #1673b8;
    --gold: #c39a38;
    --ink: #1c1c1c;
    --band-blue-dark: #0b4f8f;
    --band-blue-light: #1a6cb5;
  }
  * { margin: 0; padding: 0; box-sizing: border-box; }
  html, body { width: 1200px; height: 686px; overflow: hidden; }
  body {
    background: var(--backdrop);
    font-family: "Source Sans 3", "Myriad Pro", Arial, sans-serif;
    position: relative;
    color: var(--ink);
  }
  .card {
    position: absolute;
    width: 510px;
    height: 291px;
    background: var(--card);
    border-radius: 12px;
    overflow: hidden;
    box-shadow: 0 2px 4px rgba(0,0,0,0.35);
  }
  .card--front-centered { left: 67px; top: 37px; }
  .card--front-columns { left: 67px; top: 352px; }
  .card--back { left: 621px; top: 303px; }

  .brand {
    position: absolute;
    left: 0; right: 0;
    display: flex;
    align-items: center;
    justify-content: center;
    gap: 10px;
    color: var(--brand-blue);
    font-weight: 700;
    letter-spacing: 0.5px;
    white-space: nowrap;
  }
  .brand__mark { background: var(--brand-blue); display: block; }
  .brand--small { top: 62px; font-size: 34px; }
  .brand--small .brand__mark { width: 18px; height: 18px; }
  .brand--large { top: 110px; font-size: 44px; }
  .brand--large .brand__mark { width: 22px; height: 22px; }

  .person-line {
    position: absolute;
    top: 145px; left: 0; right: 0;
    text-align: center;
    white-space: nowrap;
  }
  .person-name { color: var(--name-blue); font-weight: 700; font-size: 17px; }
  .person-sep { display: inline-block; width: 1px; height: 14px; background: #333; margin: 0 8px; vertical-align: -1px; }
  .person-role { color: var(--gold); font-weight: 700; font-size: 13.5px; }

  .contact-center {
    position: absolute;
    top: 170px; left: 0; right: 0;
    text-align: center;
    font-size: 13px;
    line-height: 20.5px;
  }
  .contact-item { display: inline-flex; align-items: center; gap: 2px; margin: 0 4px; }
  .icon { width: 12px; height: 12px; fill: var(--name-blue); flex: none; }

  .identity {
    position: absolute;
    right: 283px; top: 156px;
    text-align: right;
    white-space: nowrap;
  }
  .identity .person-name { display: block; line-height: 20px; }
  .identity .person-role { display: block; line-height: 17px; }
  .identity .address { font-size: 13px; line-height: 16px; margin-top: 4px; }
  .divider {
    position: absolute;
    left: 251px; top: 161px;
    width: 1px; height: 60px;
    background: #555;
  }
  .contact-list {
    position: absolute;
    left: 264px; top: 156px;
    font-size: 13px;
    line-height: 19.5px;
    list-style: none;
  }
  .contact-list li { display: flex; align-items: center; gap: 3px; white-space: nowrap; }

  .footer-band { position: absolute; left: 0; bottom: 0; width: 510px; height: 28px; }
  .website {
    position: absolute;
    right: 40px; bottom: 7px;
    color: #fff;
    font-weight: 700;
    font-size: 12.5px;
    letter-spacing: 1.6px;
  }
</style>
</head>
<body>

<svg width="0" height="0" style="position:absolute" aria-hidden="true">
  <defs>
    <linearGradient id="bandBlue" x1="0" x2="1" y1="0" y2="0">
      <stop offset="0" stop-color="#0b4f8f"/>
      <stop offset="1" stop-color="#1a6cb5"/>
    </linearGradient>
    <symbol id="icon-phone" viewBox="0 0 24 24"><path d="M6.6 2.5l3 3.6-1.8 2.4c1.2 2.8 3.4 5 6.2 6.4l2.4-1.8 3.6 3-1.6 3.6c-8.4-.6-14.8-7-15.4-15.4z"/></symbol>
    <symbol id="icon-fax" viewBox="0 0 24 24"><path d="M6 2h10l2 2v5H6z M3 10h18v11H3z M6 13h4v2H6z M6 17h12v2H6z" fill-rule="evenodd"/></symbol>
    <symbol id="icon-mail" viewBox="0 0 24 24"><path d="M2 5h20v2l-10 6L2 7z M2 9l10 6 10-6v10H2z"/></symbol>
  </defs>
</svg>

<!-- Front: centered layout -->
<section class="card card--front-centered">
  <div class="brand brand--small"><span class="brand__mark"></span>DEL Varosi Group</div>
  <p class="person-line"><span class="person-name">Kerem EL Nadiri</span><span class="person-sep"></span><span class="person-role">Operation Manager</span></p>
  <div class="contact-center">
    <div>Street name City, State, zip code</div>
    <div>
      <span class="contact-item"><svg class="icon"><use href="#icon-phone"/></svg>(TF)123-456-7890</span>
      <span class="contact-item"><svg class="icon"><use href="#icon-phone"/></svg>123-456-7890</span>
    </div>
    <div>
      <span class="contact-item"><svg class="icon"><use href="#icon-fax"/></svg>123-456-7890</span>
      <span class="contact-item"><svg class="icon"><use href="#icon-mail"/></svg>name@website.com</span>
    </div>
  </div>
  <svg class="footer-band" viewBox="0 0 510 28" aria-hidden="true">
    <polygon points="0,11 294,11 286,26 0,26" fill="var(--gold)"/>
    <polygon points="306,0 510,0 510,28 284,28" fill="url(#bandBlue)"/>
  </svg>
  <span class="website">www.website.com</span>
</section>

<!-- Front: two-column layout -->
<section class="card card--front-columns">
  <div class="brand brand--small"><span class="brand__mark"></span>DEL Varosi Group</div>
  <div class="identity">
    <span class="person-name">Kerem EL Nadiri</span>
    <span class="person-role">Operation Manager</span>
    <div class="address">Street name City<br>State, zip code</div>
  </div>
  <span class="divider"></span>
  <ul class="contact-list">
    <li><svg class="icon"><use href="#icon-phone"/></svg>(TF)123-456-7890</li>
    <li><svg class="icon"><use href="#icon-phone"/></svg>123-456-7890</li>
    <li><svg class="icon"><use href="#icon-fax"/></svg>123-456-7890</li>
    <li><svg class="icon"><use href="#icon-mail"/></svg>name@website.com</li>
  </ul>
  <svg class="footer-band" viewBox="0 0 510 28" aria-hidden="true">
    <polygon points="0,11 294,11 286,26 0,26" fill="var(--gold)"/>
    <polygon points="306,0 510,0 510,28 284,28" fill="url(#bandBlue)"/>
  </svg>
  <span class="website">www.website.com</span>
</section>

<!-- Back -->
<section class="card card--back">
  <div class="brand brand--large"><span class="brand__mark"></span>DEL Varosi Group</div>
  <svg class="footer-band" viewBox="0 0 510 28" aria-hidden="true">
    <polygon points="0,11 294,11 286,26 0,26" fill="var(--gold)"/>
    <polygon points="306,0 510,0 510,28 284,28" fill="url(#bandBlue)"/>
  </svg>
  <span class="website">www.website.com</span>
</section>

</body>
</html>
```